Hydroponic company- Label for custom blended cannabis fertilizer concentrate

We need a label design for a new product we're manufacturing. It's a 2 part hydroponic fertilizer for cannabis. Our company name is Bright Reed Farms located in Trinidad and Tobago. We focus on innovative, modern and sustainable products. This fertilizer is blended based on hands on experience and tweaking to get optimal growth and yields. Label should portray explosive growth and heavy high quality yields while also being a bit fun.

The fertilizer set will consist of 4 bottles with a front and back on each. The two back labels will just be text, so no design required. The two front labels will almost be the same but with just a change in the text for the name and fertilizer ratio

We want to incorporate a personified animal on the label. Initial thoughts are a bull or wolf. muscular look but also smart and fun. Not menacing. We are open to other suggestions as well.

Target Market(s)

Cannabis growers

Requirements
Must have
• We want to incorporate a personified animal on the label. Initial thoughts are a bull or wolf. muscular look but also smart and fun. Not menacing. We are open to other suggestions as well.

```html
<!DOCTYPE html>
<html lang="en">
<head>
<meta charset="utf-8">
<title>VigorGrow – Bright Reed Farms Labels</title>
<link href="https://fonts.googleapis.com/css2?family=Montserrat:wght@900&family=Oswald:wght@400;500;600&display=swap" rel="stylesheet">
<style>
  :root {
    --page: #ffffff;
    --sky-edge: #a6daf3;
    --sky-mid: #d6effa;
    --sun-edge: #fbe84c;
    --sun-mid: #fdf5b4;
    --glow: #ffffff;
    --navy: #1d3f8f;
    --leaf: #3d9b2f;
    --band: #2e9a42;
    --band-text: #ffffff;
    --ocean: #1f5cb0;
    --art-dark: #2f3b3c;
    --art-leaf: #5f8f3a;
  }
  * { margin: 0; padding: 0; box-sizing: border-box; }
  html, body {
    width: 1200px; height: 873px; overflow: hidden;
    background: var(--page);
  }
  .label-set {
    position: relative; width: 1200px; height: 873px;
    display: flex; justify-content: center; align-items: center; gap: 44px;
  }
  .label {
    position: relative; width: 524px; height: 660px;
    border-radius: 10px; overflow: hidden;
    font-family: "Oswald", sans-serif;
  }
  .label--part-one { background: radial-gradient(ellipse 60% 52% at 50% 58%, var(--glow) 0%, var(--sky-mid) 45%, var(--sky-edge) 100%); }
  .label--part-two { background: radial-gradient(ellipse 60% 52% at 50% 58%, var(--glow) 0%, var(--sun-mid) 40%, var(--sun-edge) 100%); }

  .brand {
    position: absolute; top: 38px; left: 0; right: 0;
    display: flex; flex-direction: column; align-items: center;
  }
  .brand__name {
    display: flex; align-items: center; gap: 9px;
    font-weight: 500; font-size: 25px; letter-spacing: 3px;
    color: var(--leaf); text-transform: uppercase; line-height: 1;
  }
  .brand__dot { width: 22px; height: 22px; border-radius: 50%; background: var(--leaf); }
  .brand__tagline {
    margin-top: 5px; margin-left: 30px;
    font-size: 10.5px; letter-spacing: 1.6px; color: var(--ocean); line-height: 1;
  }

  .mascot-art {
    position: absolute; left: 88px; top: 92px; width: 348px; height: 286px;
    border-radius: 46% 46% 20% 20%;
  }
  .label--part-one .mascot-art { background: radial-gradient(ellipse at 50% 45%, #3b4e5a 0%, var(--art-dark) 45%, var(--art-leaf) 75%, rgba(95,143,58,0) 100%); }
  .label--part-two .mascot-art { background: radial-gradient(ellipse at 55% 45%, #d9822e 0%, #b9621f 40%, var(--art-leaf) 72%, rgba(95,143,58,0) 100%); }

  .part-title {
    position: absolute; top: 392px; left: 0; right: 0; text-align: center;
    font-family: "Montserrat", sans-serif; font-weight: 900;
    font-size: 38px; color: var(--navy); line-height: 1;
    transform: rotate(-3deg);
  }
  .ratio {
    position: absolute; top: 442px; left: 0; right: 0; text-align: center;
    font-weight: 600; font-size: 27px; color: var(--leaf); line-height: 1;
  }
  .descriptor {
    position: absolute; top: 480px; right: 60px;
    font-weight: 600; font-size: 11.5px; color: var(--navy); line-height: 1;
  }
  .product-name {
    position: absolute; top: 492px; left: 0; right: 0; text-align: center;
    font-family: "Oswald", sans-serif; font-weight: 600;
    font-size: 80px; line-height: 1; letter-spacing: 2px;
    color: var(--leaf);
  }

  .features {
    position: absolute; top: 592px; left: 0; right: 0;
    display: flex; justify-content: center; align-items: center;
    list-style: none;
  }
  .feature {
    display: flex; align-items: center; gap: 6px;
    padding: 0 9px;
    font-size: 9.5px; line-height: 1.2; color: var(--navy); text-transform: uppercase;
  }
  .feature + .feature { border-left: 1.5px solid var(--leaf); }
  .feature__icon { width: 24px; height: 24px; flex: none; }

  .volume-band {
    position: absolute; left: 0; right: 0; bottom: 0; height: 30px;
    background: var(--band); color: var(--band-text);
    display: flex; align-items: center; justify-content: center;
    font-weight: 500; font-size: 15px;
  }
</style>
</head>
<body>
<main class="label-set">

  <section class="label label--part-one">
    <header class="brand">
      <div class="brand__name"><span class="brand__dot"></span>Bright Reed Farms</div>
      <div class="brand__tagline">INNOVATIVE | MODERN | SUSTAINABLE</div>
    </header>
    <div class="mascot-art" role="img" aria-label="Roaring bear bursting through a cracked wall, framed by cannabis leaves"></div>
    <div class="part-title">PART 01</div>
    <div class="ratio">10-5-14</div>
    <div class="descriptor">Cannabis Fertilizer Concentrate</div>
    <h1 class="product-name">VigorGrow</h1>
    <ul class="features">
      <li class="feature">
        <svg class="feature__icon" viewBox="0 0 24 24" fill="none" stroke="#1d3f8f" stroke-width="1.4"><circle cx="12" cy="12" r="10.5"/><circle cx="12" cy="12" r="2"/><path d="M12 4v4M12 16v4M4 12h4M16 12h4M6.5 6.5l2.5 2.5M15 15l2.5 2.5M17.5 6.5L15 9M9 15l-2.5 2.5"/></svg>
        <span>Super<br>Concentrated</span>
      </li>
      <li class="feature">
        <svg class="feature__icon" viewBox="0 0 24 24" fill="none" stroke="#1d3f8f" stroke-width="1.4"><circle cx="12" cy="12" r="10.5"/><path d="M6 10h12M6 14h12M6 17h12M8 10V7M12 10V6M16 10V7"/></svg>
        <span>Great for<br>Hydro</span>
      </li>
      <li class="feature">
        <svg class="feature__icon" viewBox="0 0 24 24" fill="none" stroke="#1d3f8f" stroke-width="1.4"><circle cx="12" cy="12" r="10.5"/><path d="M8 12l3 3 5-6"/></svg>
        <span>Easy<br>to use</span>
      </li>
      <li class="feature">
        <svg class="feature__icon" viewBox="0 0 24 24" fill="none" stroke="#1d3f8f" stroke-width="1.4"><circle cx="12" cy="12" r="10.5"/><path d="M12 18v-6M12 12c0-3 2-5 5-5 0 3-2 5-5 5zM12 14c0-2-1.5-3.5-4-3.5 0 2 1.5 3.5 4 3.5z"/></svg>
        <span>Optimum<br>Nutrient</span>
      </li>
    </ul>
    <footer class="volume-band">500 ML ( 16.9 OZ )</footer>
  </section>

  <section class="label label--part-two">
    <header class="brand">
      <div class="brand__name"><span class="brand__dot"></span>Bright Reed Farms</div>
      <div class="brand__tagline">INNOVATIVE | MODERN | SUSTAINABLE</div>
    </header>
    <div class="mascot-art" role="img" aria-label="Roaring tiger bursting through a cracked wall, framed by cannabis leaves"></div>
    <div class="part-title">PART 02</div>
    <div class="ratio">10-5-14</div>
    <div class="descriptor">Cannabis Fertilizer Concentrate</div>
    <h1 class="product-name">VigorGrow</h1>
    <ul class="features">
      <li class="feature">
        <svg class="feature__icon" viewBox="0 0 24 24" fill="none" stroke="#1d3f8f" stroke-width="1.4"><circle cx="12" cy="12" r="10.5"/><circle cx="12" cy="12" r="2"/><path d="M12 4v4M12 16v4M4 12h4M16 12h4M6.5 6.5l2.5 2.5M15 15l2.5 2.5M17.5 6.5L15 9M9 15l-2.5 2.5"/></svg>
        <span>Super<br>Concentrated</span>
      </li>
      <li class="feature">
        <svg class="feature__icon" viewBox="0 0 24 24" fill="none" stroke="#1d3f8f" stroke-width="1.4"><circle cx="12" cy="12" r="10.5"/><path d="M6 10h12M6 14h12M6 17h12M8 10V7M12 10V6M16 10V7"/></svg>
        <span>Great for<br>Hydro</span>
      </li>
      <li class="feature">
        <svg class="feature__icon" viewBox="0 0 24 24" fill="none" stroke="#1d3f8f" stroke-width="1.4"><circle cx="12" cy="12" r="10.5"/><path d="M8 12l3 3 5-6"/></svg>
        <span>Easy<br>to use</span>
      </li>
      <li class="feature">
        <svg class="feature__icon" viewBox="0 0 24 24" fill="none" stroke="#1d3f8f" stroke-width="1.4"><circle cx="12" cy="12" r="10.5"/><path d="M12 18v-6M12 12c0-3 2-5 5-5 0 3-2 5-5 5zM12 14c0-2-1.5-3.5-4-3.5 0 2 1.5 3.5 4 3.5z"/></svg>
        <span>Optimum<br>Nutrient</span>
      </li>
    </ul>
    <footer class="volume-band">500 ML ( 16.9 OZ )</footer>
  </section>

</main>
</body>
</html>
```